Website for BrightlineLabs presentation

We need a new website, ideally as a wordpress there, for BrightlineLabs - we focus on machine learning, big data, data science and data analytics. This website should have two main sections - team presentation, introduction and offered services as static pages, and a blog section.

Target Market(s)

Companies which would like to hire the consultants for data science

Industry/Entity Type

Data Service

Font styles to use
Sans Serif

Colors

Designer to choose colors to be used in the design.

Requirements
Must have
• Wordpress template, blog and presentation pages, nice background images, incorporate the existing logo from brief
Nice to have
• match the word and ppt existing templates for brightline labs

```html
<!DOCTYPE html>
<html lang="en">
<head>
<meta charset="utf-8">
<title>BrightlineLabs</title>
<link rel="stylesheet" href="https://fonts.googleapis.com/css2?family=Lato:wght@300;400;700;900&family=Montserrat:wght@500;600&family=Open+Sans:wght@300;400&display=swap">
<style>
:root{
  --blue:#1589c8;
  --footer-blue:#1487c5;
  --ink:#111;
  --muted:#8a8a8a;
  --body:#555;
  --nav:#a9a9a9;
  --white:#fff;
  --card:#f2f2f2;
  --bar:#050505;
}
*{margin:0;padding:0;box-sizing:border-box}
html,body{width:923px;height:1200px;overflow:hidden;background:var(--white)}
body{position:relative;font-family:'Lato',sans-serif;color:var(--ink)}
.abs{position:absolute}

/* header */
.site-header{position:absolute;left:0;top:0;width:923px;height:97px;background:var(--white);border-bottom:2px solid #777}
.brand{position:absolute;left:60px;top:22px;display:flex;align-items:center;gap:10px}
.brand-mark{width:40px;height:40px;border-radius:50%;background:var(--blue)}
.brand-name{font-family:'Lato',sans-serif;font-weight:900;font-size:21px;line-height:21px;color:var(--blue);width:120px}
.main-nav{position:absolute;top:30px;left:421px;display:flex;align-items:center;font-family:'Open Sans',sans-serif;font-size:11px;color:var(--nav)}
.main-nav a{color:var(--nav);text-decoration:none;margin-right:45px}
.main-nav .active{color:#555;background:var(--white);border-radius:20px;box-shadow:0 3px 5px rgba(0,0,0,.35);padding:11px 23px;margin-right:22px}

/* hero */
.hero{position:absolute;left:0;top:97px;width:923px;height:385px;background:radial-gradient(ellipse at 50% 45%,#4c4c4c 0%,#2b2b2b 55%,#1b1b1b 100%);text-align:center;color:var(--white)}
.hero-title{position:absolute;left:0;right:0;top:122px;font-family:'Lato',sans-serif;font-weight:900;font-size:55px;letter-spacing:-1px;text-shadow:0 2px 4px rgba(0,0,0,.5)}
.hero-text{position:absolute;left:170px;width:583px;top:197px;font-size:14px;line-height:19px}
.hero-btn{position:absolute;left:389px;top:252px;width:144px;height:39px;border-radius:20px;background:var(--white);color:#222;font-family:'Open Sans',sans-serif;font-size:15px;line-height:39px}

/* about */
.section-title{position:absolute;left:0;right:0;top:526px;text-align:center;font-family:'Montserrat',sans-serif;font-weight:500;font-size:34px;letter-spacing:.5px}
.section-kicker{position:absolute;left:368px;width:185px;top:568px;display:flex;align-items:center;gap:9px;font-family:'Open Sans',sans-serif;font-size:11px;color:var(--blue)}
.section-kicker i{flex:1;height:1px;background:var(--blue)}
.section-intro{position:absolute;left:110px;width:703px;top:589px;text-align:center;font-family:'Open Sans',sans-serif;font-size:11.5px;line-height:17.6px;color:var(--body)}

.service{position:absolute;top:675px;width:196px;height:231px;text-align:center}
.service.featured{background:var(--card);box-shadow:0 6px 10px rgba(0,0,0,.2)}
.service-icon{position:absolute;left:57px;top:20px;width:82px;height:82px;border-radius:50%;border:2px solid var(--blue);display:flex;align-items:center;justify-content:center;background:var(--white)}
.featured .service-icon{background:var(--blue)}
.service h3{position:absolute;left:0;right:0;top:115px;font-family:'Open Sans',sans-serif;font-weight:400;font-size:15px;color:var(--blue)}
.featured h3{color:var(--ink)}
.service p{position:absolute;left:8px;right:8px;top:143px;font-family:'Open Sans',sans-serif;font-weight:300;font-size:11.5px;line-height:16px;color:var(--muted)}
.service a{position:absolute;left:0;right:0;top:185px;font-family:'Open Sans',sans-serif;font-size:11.5px;color:var(--blue);text-decoration:underline}
.featured a{color:var(--ink)}

/* footer */
.site-footer{position:absolute;left:0;top:955px;width:923px;height:203px;background:var(--footer-blue);color:var(--white);font-family:'Open Sans',sans-serif}
.footer-head{position:absolute;top:41px;font-family:'Lato',sans-serif;font-size:14px;letter-spacing:.4px}
.footer-text{position:absolute;font-size:11.5px;line-height:15px}
.email-field{position:absolute;left:59px;top:110px;width:184px;height:35px;border:1px solid var(--white);border-radius:18px;font-size:11px;padding:10px 0 0 18px}
.subscribe-btn{position:absolute;left:59px;top:149px;width:104px;height:32px;background:var(--white);border-radius:16px;color:#222;font-size:13px;line-height:32px;text-align:center}
.contact-row{position:absolute;left:262px;display:flex;gap:10px;font-size:11.5px;line-height:18px}
.post{position:absolute;left:466px;display:flex;gap:10px}
.post-thumb{width:40px;height:40px;background:linear-gradient(135deg,#0c2340,#3b6f95)}
.post h4{font-family:'Lato',sans-serif;font-weight:700;font-size:12px;line-height:13px}
.post time{display:block;margin-top:5px;font-size:9.5px}
.footer-brand{position:absolute;left:668px;top:55px;display:flex;align-items:center;gap:10px}
.footer-brand .brand-mark{background:rgba(255,255,255,.35)}
.footer-brand .brand-name{color:rgba(255,255,255,.6);font-size:18px;line-height:19px}
.call-btn{position:absolute;left:668px;top:120px;width:160px;height:32px;border-radius:16px;background:var(--white);color:#222;font-size:13px;line-height:32px;text-align:center}

.bottom-bar{position:absolute;left:0;top:1158px;width:923px;height:42px;background:var(--bar);color:var(--white);font-family:'Open Sans',sans-serif;font-size:11.5px}
.bottom-bar p{position:absolute;left:64px;top:14px}
.bottom-bar b{font-weight:700}
.bottom-bar span{color:#aaa}
.social{position:absolute;top:6px;width:29px;height:29px;border-radius:50%;border:2px solid #888}
.social.on{background:var(--white);border-color:var(--white)}
</style>
</head>
<body>

<header class="site-header">
  <div class="brand"><span class="brand-mark"></span><span class="brand-name">BRIGHTLINE LABS</span></div>
  <nav class="main-nav">
    <a class="active">HOME</a><a>ABOUT US</a><a>SERVICES</a><a>BLOG</a><a>CONTACT US</a>
  </nav>
</header>

<section class="hero" role="img" aria-label="Photo of dark server hardware with status lights">
  <h1 class="hero-title">DATA SCIENCE</h1>
  <p class="hero-text">Lorem Ipsum is simply dummy text of the printing and typesetting industry. Lorem Ipsum has been the industry's standard dummy text ever since the 1500s.</p>
  <div class="hero-btn">LEARN MORE</div>
</section>

<h2 class="section-title">KNOW ABOUT US</h2>
<div class="section-kicker"><i></i>WHO WE ARE<i></i></div>
<p class="section-intro">Lorem Ipsum is simply dummy text of the printing and typesetting industry. Lorem Ipsum has been the industry's standard dummy text ever since the 1500s, when an unknown printer took a galley of type and scrambled it to make a type specimen book. It has survived not only five centuries, but also the leap into electronic typesetting, remaining essentially unchanged.</p>

<article class="service" style="left:60px">
  <div class="service-icon"><svg width="44" height="40" viewBox="0 0 44 40" fill="none" stroke="#666" stroke-width="1.4"><rect x="2" y="3" width="40" height="26"/><path d="M18 33h8M14 36h16M22 29v4"/><rect x="7" y="9" width="9" height="10"/><path d="M26 8l10 14M36 8L26 22"/></svg></div>
  <h3>Machine learning</h3>
  <p>Lorem Ipsum is simply dummy text of the printing.</p>
  <a>LEARN MORE</a>
</article>

<article class="service" style="left:264px">
  <div class="service-icon"><svg width="44" height="40" viewBox="0 0 44 40" fill="none" stroke="#666" stroke-width="1.4"><path d="M10 26a8 8 0 0 1 2-15 10 10 0 0 1 19 1 7 7 0 0 1 3 14"/><rect x="18" y="14" width="8" height="8"/><rect x="11" y="25" width="8" height="8"/><rect x="25" y="25" width="8" height="8"/></svg></div>
  <h3>Big data</h3>
  <p>Lorem Ipsum is simply dummy text of the printing.</p>
  <a>LEARN MORE</a>
</article>

<article class="service featured" style="left:464px">
  <div class="service-icon"><svg width="44" height="44" viewBox="0 0 44 44" fill="none" stroke="#fff" stroke-width="1.4"><rect x="12" y="10" width="20" height="24"/><circle cx="22" cy="22" r="4"/><ellipse cx="22" cy="22" rx="8" ry="3"/><path d="M6 14h6M6 22h6M6 30h6M32 14h6M32 22h6M32 30h6M18 4v6M26 4v6M18 34v6M26 34v6"/></svg></div>
  <h3>Data science</h3>
  <p>Lorem Ipsum is simply dummy text of the printing.</p>
  <a>LEARN MORE</a>
</article>

<article class="service" style="left:668px">
  <div class="service-icon"><svg width="46" height="40" viewBox="0 0 46 40" fill="none" stroke="#666" stroke-width="1.4"><path d="M3 37h40"/><rect x="7" y="25" width="5" height="12"/><rect x="16" y="19" width="5" height="18"/><rect x="25" y="23" width="5" height="14"/><rect x="34" y="13" width="5" height="24"/><path d="M7 15l10-5 9 4 12-9"/><circle cx="7" cy="15" r="2"/><circle cx="17" cy="10" r="2"/><circle cx="26" cy="14" r="2"/><circle cx="38" cy="5" r="2"/></svg></div>
  <h3>Data analytics</h3>
  <p>Lorem Ipsum is simply dummy text of the printing.</p>
  <a>LEARN MORE</a>
</article>

<footer class="site-footer">
  <h4 class="footer-head" style="left:62px">Newsletter</h4>
  <p class="footer-text" style="left:61px;top:72px;width:190px">Subscribe to Our Newsletter to Get Latest Updates &amp; News.</p>
  <div class="email-field">E-mail Id</div>
  <div class="subscribe-btn">SUBSCRIBE</div>

  <h4 class="footer-head" style="left:264px">Contact Us</h4>
  <div class="contact-row" style="top:72px">
    <svg width="16" height="20" viewBox="0 0 16 20" fill="none" stroke="#fff" stroke-width="1.2"><path d="M8 19s-7-7-7-11a7 7 0 0 1 14 0c0 4-7 11-7 11z"/><circle cx="8" cy="8" r="2.5"/></svg>
    <span>123 Building Name, Street,<br>City, Country - Zipcode</span>
  </div>
  <div class="contact-row" style="top:112px">
    <svg width="18" height="18" viewBox="0 0 18 18" fill="none" stroke="#fff" stroke-width="1.2"><path d="M2 3l4-1 2 4-2 2a10 10 0 0 0 4 4l2-2 4 2-1 4C8 16 2 10 2 3z"/></svg>
    <span>123 456 7878</span>
  </div>
  <div class="contact-row" style="top:143px">
    <svg width="20" height="16" viewBox="0 0 20 16" fill="none" stroke="#fff" stroke-width="1.2"><rect x="1" y="2" width="18" height="12"/><path d="M1 2l9 7 9-7M1 14l7-6M19 14l-7-6"/></svg>
    <span>info@brightlinelabs.com</span>
  </div>

  <h4 class="footer-head" style="left:468px">Latest Post</h4>
  <div class="post" style="top:72px">
    <div class="post-thumb" role="img" aria-label="Photo of a lit server room aisle"></div>
    <div><h4>Lorem Ipsum is simply<br>dummy text of</h4><time>Today 5:60 pm - 12.06.2018</time></div>
  </div>
  <div class="post" style="top:128px">
    <div class="post-thumb" role="img" aria-label="Photo of a desk with a laptop" style="background:linear-gradient(135deg,#8a93a8,#3d4b6e)"></div>
    <div><h4>Lorem Ipsum is simply<br>dummy text of</h4><time>Today 5:60 pm - 12.06.2018</time></div>
  </div>

  <div class="footer-brand"><span class="brand-mark"></span><span class="brand-name">BRIGHTLINE LABS</span></div>
  <div class="call-btn">SCHEDULE A CALL</div>
</footer>

<div class="bottom-bar">
  <p>© <b>BRIGHTLINE LABS - 2018.</b> <span>All Rights Reserved</span></p>
  <span class="social on" style="left:734px"></span>
  <span class="social" style="left:767px"></span>
  <span class="social" style="left:800px"></span>
</div>

</body>
</html>
```